Tolvik Commercial Cleaning is lookong for a new business card design.

A fresh new design that's professional and stylish. We need a serious upgrade to our business cards. I have included pictures of our existing ones. Our clients include professional individuals and business owners. We woupdblike something professional and upbeat. Please have fun and see what you come uo with.

Target Market(s)

Property managers, business owners, facility managers and other similar professionals

Industry/Entity Type

Janitorial

Contact Information for Business Card

Name, cell, office number, email, web address

Font styles to use
Sans Serif

Colors

Designer to choose colors to be used in the design.

Requirements
Must have
• please use the green color in our logo
Nice to have
• Bar code
Should not have
• Address

```html
<!DOCTYPE html>
<html lang="en">
<head>
<meta charset="utf-8">
<title>Tolvik Commercial Cleaning – Business Card</title>
<link rel="stylesheet" href="https://fonts.googleapis.com/css2?family=Open+Sans:wght@400;700&display=swap">
<style>
  :root {
    --card-dark: #202024;
    --brand-green: #3bb75a;
    --brand-blue: #3d72ad;
    --text-light: #f2f2f2;
    --backdrop: #e6e6e3;
  }
  html, body {
    margin: 0;
    padding: 0;
    width: 1200px;
    height: 780px;
    overflow: hidden;
    background: var(--backdrop);
    font-family: "Open Sans", Arial, sans-serif;
  }
  .canvas {
    position: relative;
    width: 1200px;
    height: 780px;
  }
  .card {
    position: absolute;
    top: 236px;
    width: 540px;
    height: 309px;
    border-radius: 18px;
    background: var(--card-dark);
    overflow: hidden;
    box-shadow: 0 6px 18px rgba(0,0,0,0.18);
  }
  .card--front { left: 40px; }
  .card--back { left: 620px; }

  /* front side */
  .edge-strip {
    position: absolute;
    left: 0;
    bottom: 0;
    width: 540px;
    height: 18px;
  }
  .front-brand {
    position: absolute;
    left: 34px;
    top: 48px;
    width: 220px;
    color: var(--brand-green);
    font-weight: 700;
    line-height: 1.05;
  }
  .front-brand .brand-name { font-size: 46px; display: block; letter-spacing: 0.5px; }
  .front-brand .brand-line { font-size: 17px; display: block; margin-top: 6px; }
  .divider {
    position: absolute;
    left: 0;
    top: 0;
    width: 540px;
    height: 309px;
  }
  .holder {
    position: absolute;
    left: 300px;
    top: 112px;
  }
  .holder-name {
    margin: 0 0 14px;
    font-size: 26px;
    font-weight: 700;
    white-space: nowrap;
  }
  .holder-name .first { color: var(--brand-green); }
  .holder-name .last { color: var(--brand-blue); }
  .contact-list {
    list-style: none;
    margin: 0;
    padding: 0;
    color: var(--text-light);
    font-size: 14px;
  }
  .contact-list li {
    display: flex;
    align-items: center;
    gap: 8px;
    height: 24px;
  }
  .contact-icon { width: 14px; height: 14px; flex: none; }

  /* back side */
  .green-band {
    position: absolute;
    left: 0;
    top: 36px;
    width: 540px;
    height: 200px;
    background: var(--brand-green);
    display: flex;
    flex-direction: column;
    align-items: center;
    justify-content: center;
  }
  .back-brand {
    color: #ffffff;
    font-weight: 700;
    text-align: center;
    line-height: 1;
  }
  .back-brand .brand-name { font-size: 78px; display: block; letter-spacing: 1px; }
  .back-brand .brand-line { font-size: 22px; display: block; margin-top: 10px; }
</style>
</head>
<body>
<main class="canvas">

  <section class="card card--front" aria-label="Business card front">
    <div class="front-brand">
      <span class="brand-name">Tolvik</span>
      <span class="brand-line">commercial cleaning</span>
    </div>

    <svg class="divider" viewBox="0 0 540 309" aria-hidden="true">
      <defs>
        <linearGradient id="dividerFade" x1="0" y1="0" x2="0" y2="1">
          <stop offset="0" stop-color="#ffffff" stop-opacity="0"/>
          <stop offset="0.5" stop-color="#ffffff" stop-opacity="0.9"/>
          <stop offset="1" stop-color="#ffffff" stop-opacity="0"/>
        </linearGradient>
      </defs>
      <line x1="292" y1="62" x2="236" y2="248" stroke="url(#dividerFade)" stroke-width="1.4"/>
    </svg>

    <div class="holder">
      <h1 class="holder-name"><span class="first">Marco</span> <span class="last">Deveaux</span></h1>
      <ul class="contact-list">
        <li>
          <svg class="contact-icon" viewBox="0 0 14 14" aria-hidden="true"><path d="M3 1.5 5 1l1.2 3-1.3 1a7 7 0 0 0 3.6 3.6l1-1.3 3 1.2-.5 2C11.5 11.8 10 12.6 8 12 5 11 3 9 2 6c-.6-2 .2-3.5 1-4.5z" fill="var(--brand-green)"/></svg>
          (555) 014-2290
        </li>
        <li>
          <svg class="contact-icon" viewBox="0 0 14 14" aria-hidden="true"><rect x="1" y="3" width="12" height="8.5" rx="1" fill="var(--brand-green)"/><path d="M1.5 3.6 7 8l5.5-4.4" fill="none" stroke="var(--card-dark)" stroke-width="1.2"/></svg>
          marco@tolvikcleaning.com
        </li>
        <li>
          <svg class="contact-icon" viewBox="0 0 14 14" aria-hidden="true"><circle cx="7" cy="7" r="6" fill="var(--brand-green)"/><path d="M1 7h12M7 1c-2.2 2-2.2 10 0 12M7 1c2.2 2 2.2 10 0 12" fill="none" stroke="var(--card-dark)" stroke-width="1"/></svg>
          www.tolvikcleaning.com
        </li>
      </ul>
    </div>

    <svg class="edge-strip" viewBox="0 0 540 18" preserveAspectRatio="none" aria-hidden="true">
      <polygon points="0,0 168,0 158,18 0,18" fill="var(--brand-green)"/>
      <polygon points="168,0 540,0 540,18 158,18" fill="var(--brand-blue)"/>
    </svg>
  </section>

  <section class="card card--back" aria-label="Business card back">
    <div class="green-band">
      <div class="back-brand">
        <span class="brand-name">Tolvik</span>
        <span class="brand-line">commercial cleaning</span>
      </div>
    </div>
  </section>

</main>
</body>
</html>
```